I need a business card for my original fine art pieces

I would like a business card design including a logo design for a new business in the art world. I am based in the Hunter Valley NSW Australia. I am a contemporary figurative, encaustic and wildlife artist. I would like to be able to upload my email and mobile number to this as well. This design should be one that I can incorporate into banners and flyers etc. Id like to incorporate one of my own images or partial image into the background or somewhere below. My initials are RJ and I would like these used as a logo type. I would like the use of some colour and it to be bright and catchy. The final design should communicate artwork custom made and commissions available.

Overview: Original Fine Artworks for sale, online, art galleries etc, Custom made to order and by commission.

Target market is world wide audience and corporate world

My figurative work is painted using acrylics in a lot of natural ochre colours that reflect the Australian Outback, on canvas, linen, paper or board: My encaustic work is created in a contemporary abstract style using a blow torch and a made with a medium of 100% pure bees wax, Damar resin, mixed media and coloured pigments, applied to Birch board. My wildlife are created using coloured pencil and mixed media on a variety of paper types or board.

```html
<!DOCTYPE html>
<html lang="en">
<head>
<meta charset="utf-8">
<title>Rosa Jennings – Business Card</title>
<link rel="stylesheet" href="https://fonts.googleapis.com/css2?family=Cinzel:wght@500&family=Arimo&family=Source+Sans+3:wght@400;600&display=swap">
<style>
  :root {
    --page-bg: #ecebe8;
    --card-black: #000000;
    --accent-orange: #ff4a00;
    --wave-grey: #4d4d4d;
    --text-white: #ffffff;
  }
  * { margin: 0; padding: 0; box-sizing: border-box; }
  html, body {
    width: 1200px; height: 900px; overflow: hidden;
    background: var(--page-bg);
  }
  .business-card {
    position: absolute; left: 111px; top: 147px;
    width: 978px; height: 605px;
    background: var(--card-black);
    overflow: hidden;
    box-shadow: 0 6px 24px rgba(0,0,0,0.18);
  }
  .card-wave { position: absolute; inset: 0; width: 100%; height: 100%; }
  .brand-ring {
    position: absolute; left: 179px; top: 64px;
    width: 164px; height: 164px;
    border: 4px solid var(--accent-orange); border-radius: 50%;
  }
  .brand-name {
    position: absolute; left: 0; width: 524px; top: 236px;
    text-align: center;
    font-family: "Cinzel", serif; font-weight: 500;
    font-size: 50px; line-height: 1; color: var(--accent-orange);
    white-space: nowrap;
  }
  .brand-tagline {
    position: absolute; left: 0; width: 524px; top: 287px;
    text-align: center;
    font-family: "Arimo", sans-serif; font-size: 21px; line-height: 1;
    letter-spacing: 4px; color: var(--text-white); white-space: nowrap;
  }
  .contact {
    position: absolute; right: 50px;
    font-family: "Source Sans 3", sans-serif; color: var(--text-white);
    text-align: right; white-space: nowrap; line-height: 1;
  }
  .contact-name { top: 278px; font-size: 31px; font-weight: 600; }
  .contact-role { top: 315px; font-size: 24px; }
  .contact-line { font-size: 24px; display: flex; align-items: center; gap: 14px; }
  .contact-phone { top: 375px; }
  .contact-email { top: 411px; }
  .contact-web { top: 446px; }
  .contact-address { top: 514px; font-size: 24px; }
  .contact-icon { width: 18px; height: 18px; flex: none; }
</style>
</head>
<body>
  <div class="business-card">
    <svg class="card-wave" viewBox="0 0 652 403" preserveAspectRatio="none" aria-hidden="true">
      <path fill="var(--wave-grey)" d="M0,212 C55,285 105,312 165,312 C290,310 385,150 520,118 C585,104 630,135 652,160 L652,403 L0,403 Z"/>
      <path fill="var(--card-black)" d="M0,224 C58,297 108,324 168,324 C295,320 390,160 525,130 C590,117 632,146 652,166 L652,403 L0,403 Z"/>
      <path fill="var(--accent-orange)" d="M0,235 C60,302 110,322 170,320 C300,316 400,160 540,136 C600,127 636,155 652,172 L652,403 L0,403 Z"/>
    </svg>

    <div class="brand-ring"></div>
    <div class="brand-name">Rosa Jennings</div>
    <div class="brand-tagline">ORIGINAL FINE ARTWORKS</div>

    <div class="contact contact-name">Daniel Hart</div>
    <div class="contact contact-role">Managing Director</div>
    <div class="contact contact-line contact-phone">
      <span>044-987 654 321</span>
      <svg class="contact-icon" viewBox="0 0 24 24" aria-hidden="true"><path fill="#fff" d="M6.6 10.8a15.1 15.1 0 0 0 6.6 6.6l2.2-2.2c.3-.3.7-.4 1-.2 1.1.4 2.3.6 3.6.6.6 0 1 .4 1 1V20c0 .6-.4 1-1 1A17 17 0 0 1 3 4c0-.6.4-1 1-1h3.5c.6 0 1 .4 1 1 0 1.3.2 2.5.6 3.6.1.3 0 .7-.2 1l-2.3 2.2z"/></svg>
    </div>
    <div class="contact contact-line contact-email">
      <span>hello@studioname.com</span>
      <svg class="contact-icon" viewBox="0 0 24 24" aria-hidden="true"><rect x="2" y="5" width="20" height="14" fill="#fff"/><path d="M2 5l10 8 10-8" fill="none" stroke="var(--accent-orange)" stroke-width="2"/></svg>
    </div>
    <div class="contact contact-line contact-web">
      <span>www.studioname.com</span>
      <svg class="contact-icon" viewBox="0 0 24 24" aria-hidden="true"><g fill="none" stroke="#fff" stroke-width="2"><circle cx="12" cy="12" r="9"/><ellipse cx="12" cy="12" rx="4" ry="9"/><path d="M3 12h18M5 7h14M5 17h14"/></g></svg>
    </div>
    <div class="contact contact-address">12345, Address Goes Here Country Name, 123456.</div>
  </div>
</body>
</html>
```